Kentucky residential recovery center needs a flyer design

We need a flyer design for a 16 bed male residential/inpatient recovery center based in Richmond, Kentucky. The facility provides short term (average 30 day) treatment to those struggling with substace abuse and addiction. The design should communicate trust, assurance, safety.
Our wesite provides more information https://corvalmend.org/treatment-services/residential-treatment/

Target Market(s)

Men (typically 30-50) struggling with substance addiction

```html
<!DOCTYPE html>
<html lang="en">
<head>
<meta charset="utf-8">
<title>Corvalmend Health – Residential / Inpatient Treatment Flyer</title>
<link rel="stylesheet" href="https://fonts.googleapis.com/css2?family=Archivo+Black&family=Libre+Baskerville:wght@700&family=Poppins:wght@400;500;600;700&display=swap">
<style>
  :root {
    --navy: #0e0f7d;
    --green: #07992a;
    --sky: #5aaae6;
    --white: #ffffff;
    --ink: #1b1b2a;
    --stage: #f1f2f5;
    --badge: #c9ccd6;
  }
  * { box-sizing: border-box; margin: 0; padding: 0; }
  html, body { width: 820px; height: 1200px; overflow: hidden; background: var(--stage); }
  body { font-family: "Poppins", sans-serif; color: var(--ink); position: relative; }

  .sheet { position: absolute; left: 186px; width: 447px; height: 578px; overflow: hidden; box-shadow: 0 4px 14px rgba(0,0,0,.18); background: var(--white); }
  .sheet.front { top: 14px; }
  .sheet.back { top: 606px; }
  .page { position: absolute; left: 0; top: 0; width: 600px; height: 776px; transform: scale(0.745); transform-origin: 0 0; background: var(--white); overflow: hidden; }
  .page > * { position: absolute; }
  .art { left: 0; top: 0; width: 600px; height: 400px; }

  /* front */
  .brand { left: 28px; top: 22px; width: 96px; height: 96px; border-radius: 50%; background: var(--white); display: flex; align-items: center; justify-content: center; text-align: center; font-weight: 700; font-size: 13px; line-height: 1.2; color: var(--navy); }
  .spaces { left: 66px; top: 120px; font-family: "Archivo Black", sans-serif; color: var(--navy); font-size: 40px; letter-spacing: -1px; line-height: 1; }
  .available { left: 67px; top: 164px; font-family: "Archivo Black", sans-serif; color: var(--white); font-size: 25px; line-height: 1; }
  .program { left: 66px; top: 198px; font-family: "Libre Baskerville", serif; font-weight: 700; color: var(--navy); font-size: 21px; line-height: 25px; }
  .note { left: 69px; top: 276px; width: 170px; color: var(--white); font-size: 6.5px; line-height: 1.35; }

  .kicker { left: 0; width: 600px; text-align: center; color: var(--green); font-size: 15px; }
  .problems { top: 350px; }
  .issues { top: 388px; left: 28px; width: 541px; height: 112px; background: var(--green); display: flex; padding-top: 36px; }
  .issue { flex: 1; display: flex; flex-direction: column; align-items: center; color: var(--white); font-weight: 600; font-size: 10px; text-align: center; line-height: 1.25; border-left: 1px solid rgba(255,255,255,.35); }
  .issue:first-child { border-left: none; }
  .issue svg { width: 28px; height: 28px; margin-bottom: 10px; flex: none; }
  .issues-banner { top: 375px; left: 84px; width: 430px; height: 32px; background: var(--navy); clip-path: polygon(4% 0, 96% 0, 100% 100%, 0 100%); color: var(--white); font-family: "Libre Baskerville", serif; font-weight: 700; font-size: 16px; display: flex; align-items: center; justify-content: center; }

  .section-title { left: 0; width: 600px; text-align: center; font-family: "Libre Baskerville", serif; font-weight: 700; color: var(--green); font-size: 18px; line-height: 1; }
  .why { top: 510px; }
  .stats { top: 538px; left: 28px; width: 541px; height: 90px; display: flex; }
  .stat { flex: 1; color: var(--white); text-align: center; padding-top: 10px; }
  .stat.dark { background: var(--navy); }
  .stat.light { background: var(--sky); }
  .stat .num { font-family: "Libre Baskerville", serif; font-weight: 700; font-size: 18px; line-height: 1; }
  .stat .label { font-size: 5.5px; font-weight: 700; text-transform: uppercase; margin-top: 6px; line-height: 1.25; padding: 0 30px; }
  .stat .desc { font-size: 5.5px; margin-top: 8px; line-height: 1.3; padding: 0 24px; opacity: .9; }

  .help { top: 642px; left: 28px; font-size: 10px; font-weight: 500; }
  .help strong { display: block; color: var(--green); font-weight: 700; margin-top: 6px; }
  .transport { top: 642px; left: 385px; font-weight: 700; color: var(--navy); font-size: 12.5px; line-height: 1.45; }

  /* shared footer */
  .wave { left: 0; top: 686px; width: 600px; height: 90px; }
  .footer { left: 28px; top: 705px; width: 560px; display: flex; gap: 14px; }
  .call .cta { font-family: "Archivo Black", sans-serif; color: var(--green); font-size: 16px; line-height: 1.2; }
  .call .phone { color: var(--white); font-weight: 700; font-size: 13.5px; display: flex; align-items: center; gap: 5px; margin-top: 3px; }
  .site { padding-top: 8px; }
  .site .name { color: var(--green); font-weight: 700; font-size: 7px; text-transform: uppercase; }
  .site .addr { color: var(--white); font-size: 7px; display: flex; align-items: center; gap: 5px; margin-top: 8px; white-space: nowrap; }
  .icon-dot { width: 13px; height: 13px; flex: none; }

  /* back */
  .stages { top: 274px; }
  .how { top: 298px; color: var(--navy); font-size: 18px; }
  .step { top: 327px; width: 150px; height: 75px; background: var(--sky); color: var(--white); font-size: 6.5px; line-height: 1.4; padding: 14px 14px 0 34px; }
  .step-icon { top: 338px; width: 52px; height: 52px; }
  .testimonials { top: 413px; }
  .quote { top: 448px; width: 236px; height: 137px; border: 2px solid var(--navy); border-radius: 8px; }
  .quote p { position: absolute; left: 22px; top: 26px; width: 190px; font-size: 7.5px; line-height: 1.3; color: var(--ink); }
  .quote .who { position: absolute; right: 26px; top: 110px; font-family: "Libre Baskerville", serif; font-weight: 700; color: var(--green); font-size: 11px; }
  .mark { position: absolute; background: var(--white); color: var(--green); font-family: "Libre Baskerville", serif; font-weight: 700; font-size: 34px; line-height: 1; padding: 0 4px; height: 28px; }
  .mark.open { left: -10px; top: -14px; }
  .mark.close { right: -14px; bottom: -14px; }
  .insurers { top: 604px; }
  .insure-note { top: 632px; left: 40px; width: 520px; text-align: center; font-size: 7.5px; line-height: 1.35; }
  .badges { top: 662px; left: 28px; width: 544px; display: flex; justify-content: space-between; align-items: center; }
  .badges span { width: 46px; height: 11px; border-radius: 3px; background: var(--badge); }
</style>
</head>
<body>

<div class="sheet front">
<main class="page">
  <svg class="art" viewBox="0 0 600 400">
    <defs>
      <linearGradient id="fistsTone" x1="0" y1="0" x2="1" y2="1">
        <stop offset="0" stop-color="#e6e8ec"/><stop offset="0.55" stop-color="#a89584"/><stop offset="1" stop-color="#5b4a3e"/>
      </linearGradient>
      <linearGradient id="roomTone" x1="0" y1="0" x2="1" y2="1">
        <stop offset="0" stop-color="#c7b28c"/><stop offset="1" stop-color="#5e4a33"/>
      </linearGradient>
    </defs>
    <path d="M0 0 H600 V140 C480 300 320 345 0 345 Z" fill="var(--navy)"/>
    <circle cx="419" cy="186" r="222" fill="var(--white)"/>
    <circle cx="419" cy="186" r="215" fill="url(#fistsTone)" role="img" aria-label="Photo: a circle of joined fists seen from below against a bright sky"/>
    <circle cx="154" cy="212" r="128" fill="var(--green)"/>
    <g stroke="var(--navy)" stroke-width="3">
      <circle cx="324" cy="287" r="37" fill="url(#roomTone)" role="img" aria-label="Photo: residential bedroom"/>
      <circle cx="427" cy="302" r="37" fill="url(#roomTone)" role="img" aria-label="Photo: bunk beds in shared room"/>
      <circle cx="527" cy="282" r="37" fill="url(#roomTone)" role="img" aria-label="Photo: lounge with sofa"/>
    </g>
  </svg>

  <div class="brand">Corvalmend<br>Health</div>
  <div class="spaces">SPACES</div>
  <div class="available">AVAILABLE!</div>
  <div class="program">RESIDENTIAL/<br>INPATIENT<br>TREATMENT</div>
  <p class="note">The program has a small capacity of 16 men, split into two groups of 8. This ensures treatment is individualised.</p>

  <div class="kicker problems">PROBLEMS WE CAN HELP WITH</div>
  <section class="issues">
    <div class="issue"><svg viewBox="0 0 42 42"><circle cx="21" cy="21" r="19" fill="none" stroke="#fff" stroke-width="2.5"/><rect x="17" y="11" width="8" height="20" rx="3" fill="#fff" transform="rotate(35 21 21)"/></svg>ALCOHOLISM</div>
    <div class="issue"><svg viewBox="0 0 42 42"><circle cx="21" cy="21" r="19" fill="none" stroke="#fff" stroke-width="2.5"/><rect x="19" y="9" width="5" height="22" rx="1" fill="#fff" transform="rotate(45 21 21)"/></svg>DRUG ADDICTION</div>
    <div class="issue"><svg viewBox="0 0 42 42"><circle cx="21" cy="21" r="19" fill="none" stroke="#fff" stroke-width="2.5"/><circle cx="17" cy="24" r="6" fill="#fff"/><circle cx="25" cy="18" r="6" fill="#fff"/></svg>MEDICATION<br>ADDICTION</div>
    <div class="issue"><svg viewBox="0 0 42 42"><circle cx="21" cy="21" r="19" fill="none" stroke="#fff" stroke-width="2.5"/><circle cx="21" cy="20" r="8" fill="none" stroke="#fff" stroke-width="2.5"/><circle cx="21" cy="20" r="3" fill="#fff"/></svg>BEHAVIORAL<br>HEALTH</div>
  </section>
  <div class="issues-banner">WHAT ISSUES CAN BE TREATED?</div>

  <h2 class="section-title why">WHY &nbsp;CHOOSE US?</h2>
  <section class="stats">
    <div class="stat dark"><div class="num">100+</div><div class="label">Years</div><div class="desc">Over 100 years of medical and clinical experience behind our team</div></div>
    <div class="stat light"><div class="num">95%</div><div class="label">Satisfaction rating</div><div class="desc">Our patients rate us 95 out of 100</div></div>
    <div class="stat dark"><div class="num">#1</div><div class="label">Best drug &amp; alcohol rehab center</div><div class="desc">Voted one of the best Alcohol and Drug rehab centers</div></div>
    <div class="stat light"><div class="num">2,500+</div><div class="label">Patients treated</div><div class="desc">Over 2,500 patients treated successfully and counting</div></div>
  </section>

  <p class="help">Our caring team will help answer any questions you have<strong>GET IN TOUCH WITH US NOW. WE'RE HERE TO HELP!</strong></p>
  <p class="transport">FREE TRANSPORT<br>ASSISTANCE AVAILABLE</p>

  <svg class="wave" viewBox="0 0 600 90" preserveAspectRatio="none" aria-hidden="true">
    <path d="M0 10 Q15 0 30 10 T60 10 T90 10 T120 10 T150 10 T180 10 T210 10 T240 10 T270 10 T300 10 T330 10 T360 10 T390 10 T420 10 T450 10 T480 10 T510 10 T540 10 T570 10 T600 10 V90 H0 Z" fill="var(--navy)"/>
  </svg>
  <footer class="footer">
    <div class="call">
      <div class="cta">CALL US NOW!</div>
      <div class="phone"><svg class="icon-dot" viewBox="0 0 18 18"><circle cx="9" cy="9" r="9" fill="var(--green)"/><path d="M6 4.5 L8 6.8 L7 8 Q8 10 10 11 L11.2 10 L13.5 12 L12.3 13.5 Q8 13.5 4.5 8 Z" fill="#fff"/></svg>859-555-0142</div>
    </div>
    <div class="site">
      <div class="name">Corvalmend Health Burlington, Kentucky</div>
      <div class="addr"><svg class="icon-dot" viewBox="0 0 18 18"><circle cx="9" cy="9" r="9" fill="var(--green)"/><path d="M9 3.5 A3.5 3.5 0 0 1 12.5 7 C12.5 9.5 9 13.5 9 13.5 C9 13.5 5.5 9.5 5.5 7 A3.5 3.5 0 0 1 9 3.5 Z" fill="#fff"/></svg>4820 Meadowgate Dr, Burlington, KY 41005</div>
    </div>
    <div class="site">
      <div class="name">Corvalmend Health Richmond, Kentucky</div>
      <div class="addr"><svg class="icon-dot" viewBox="0 0 18 18"><circle cx="9" cy="9" r="9" fill="var(--green)"/><path d="M9 3.5 A3.5 3.5 0 0 1 12.5 7 C12.5 9.5 9 13.5 9 13.5 C9 13.5 5.5 9.5 5.5 7 A3.5 3.5 0 0 1 9 3.5 Z" fill="#fff"/></svg>4820 Meadowgate Dr, Burlington, KY 41005</div>
    </div>
  </footer>
</main>
</div>

<div class="sheet back">
<main class="page">
  <svg class="art" viewBox="0 0 600 400">
    <defs>
      <linearGradient id="guestTone" x1="0" y1="0" x2="0" y2="1">
        <stop offset="0" stop-color="#7f9fd0"/><stop offset="0.6" stop-color="#8b8a8f"/><stop offset="1" stop-color="#6a5444"/>
      </linearGradient>
      <linearGradient id="lodgeTone" x1="0" y1="0" x2="1" y2="1">
        <stop offset="0" stop-color="#d8cdb8"/><stop offset="0.6" stop-color="#8f7654"/><stop offset="1" stop-color="#54452f"/>
      </linearGradient>
    </defs>
    <path d="M0 0 H330 V60 C320 200 250 265 0 268 Z" fill="var(--navy)"/>
    <circle cx="445" cy="105" r="168" fill="var(--white)"/>
    <circle cx="445" cy="105" r="162" fill="url(#lodgeTone)" role="img" aria-label="Photo: resident room with sofa and wooden bunk beds"/>
    <circle cx="155" cy="132" r="130" fill="url(#guestTone)" stroke="var(--green)" stroke-width="4" role="img" aria-label="Photo: program graduate holding his completion certificate"/>
  </svg>

  <div class="kicker stages">STAGES OF RESIDENTIAL RECOVERY PROCESS</div>
  <h2 class="section-title how">HOW DOES IT WORK?</h2>

  <div class="step" style="left:52px">Speak with our team in private about the nature of your challenges and what you need help with</div>
  <div class="step" style="left:235px">Together we select an appropriate time slot to book you in for an induction appointment with one of our clinical staff</div>
  <div class="step" style="left:420px">Once the induction is completed, we'll schedule you in to commence your inpatient program</div>
  <svg class="step-icon" style="left:27px" viewBox="0 0 52 52"><circle cx="26" cy="26" r="25" fill="var(--green)" stroke="#fff" stroke-width="2"/><path d="M15 16 H33 V29 H22 L17 33 V29 H15 Z" fill="#fff"/><path d="M35 21 H38 V33 H36 V36 L32 33 H24 V31 H35 Z" fill="#fff"/></svg>
  <svg class="step-icon" style="left:210px" viewBox="0 0 52 52"><circle cx="26" cy="26" r="25" fill="var(--green)" stroke="#fff" stroke-width="2"/><rect x="15" y="17" width="22" height="19" rx="2" fill="#fff"/><rect x="15" y="17" width="22" height="5" fill="#cfe9d5"/><path d="M20 29 L24 32 L32 25" fill="none" stroke="var(--green)" stroke-width="2.5"/></svg>
  <svg class="step-icon" style="left:395px" viewBox="0 0 52 52"><circle cx="26" cy="26" r="25" fill="var(--green)" stroke="#fff" stroke-width="2"/><circle cx="26" cy="26" r="12" fill="#fff"/><path d="M23 20 L32 26 L23 32 Z" fill="var(--green)"/></svg>

  <h2 class="section-title testimonials">TESTIMONIALS</h2>
  <div class="quote" style="left:46px">
    <span class="mark open">&ldquo;</span>
    <p>Great people, they changed my life in so many ways. Caleb stopped his daily life to come to court with me to help me out of a bad spot. They're not just a doc office, they're people who want to make a difference. I love u all thanks for the help u have given me</p>
    <span class="who">Marcus T</span>
    <span class="mark close">&rdquo;</span>
  </div>
  <div class="quote" style="left:314px">
    <span class="mark open">&ldquo;</span>
    <p>For 20 years I did nothing but dope, heroin, meth and pain pills. After being in prison twice, I decided to get help at Corvalmend Health. It's been three years now and I haven't relapsed, this is the best I've ever been. Corvalmend Health support you a lot, they actually care about you.</p>
    <span class="who">Dale Whitfield</span>
    <span class="mark close">&rdquo;</span>
  </div>

  <h2 class="section-title insurers">MOST INSURANCES ACCEPTED</h2>
  <p class="insure-note">We accept most major Kentucky Medicaid and Commercial insurers. Your plan will usually cover the cost of our treatment services leaving no cost to you. Speak to us to find out more.</p>
  <div class="badges" role="img" aria-label="Accepted insurer badges">
    <span></span><span></span><span></span><span></span><span></span><span></span><span></span><span></span><span></span>
  </div>

  <svg class="wave" viewBox="0 0 600 90" preserveAspectRatio="none" aria-hidden="true">
    <path d="M0 10 Q15 0 30 10 T60 10 T90 10 T120 10 T150 10 T180 10 T210 10 T240 10 T270 10 T300 10 T330 10 T360 10 T390 10 T420 10 T450 10 T480 10 T510 10 T540 10 T570 10 T600 10 V90 H0 Z" fill="var(--navy)"/>
  </svg>
  <footer class="footer">
    <div class="call">
      <div class="cta">CALL US NOW!</div>
      <div class="phone"><svg class="icon-dot" viewBox="0 0 18 18"><circle cx="9" cy="9" r="9" fill="var(--green)"/><path d="M6 4.5 L8 6.8 L7 8 Q8 10 10 11 L11.2 10 L13.5 12 L12.3 13.5 Q8 13.5 4.5 8 Z" fill="#fff"/></svg>859-555-0142</div>
    </div>
    <div class="site">
      <div class="name">Corvalmend Health Burlington, Kentucky</div>
      <div class="addr"><svg class="icon-dot" viewBox="0 0 18 18"><circle cx="9" cy="9" r="9" fill="var(--green)"/><path d="M9 3.5 A3.5 3.5 0 0 1 12.5 7 C12.5 9.5 9 13.5 9 13.5 C9 13.5 5.5 9.5 5.5 7 A3.5 3.5 0 0 1 9 3.5 Z" fill="#fff"/></svg>4820 Meadowgate Dr, Burlington, KY 41005</div>
    </div>
    <div class="site">
      <div class="name">Corvalmend Health Richmond, Kentucky</div>
      <div class="addr"><svg class="icon-dot" viewBox="0 0 18 18"><circle cx="9" cy="9" r="9" fill="var(--green)"/><path d="M9 3.5 A3.5 3.5 0 0 1 12.5 7 C12.5 9.5 9 13.5 9 13.5 C9 13.5 5.5 9.5 5.5 7 A3.5 3.5 0 0 1 9 3.5 Z" fill="#fff"/></svg>4820 Meadowgate Dr, Burlington, KY 41005</div>
    </div>
  </footer>
</main>
</div>

</body>
</html>
```